Bright Harbor Goods - Product Page

Looking for a design for our product pages to showcase all of the following information in an aesthetically pleasing way. <br/><br/>• Product price per piece & price breaks<br/>• Set up cost <br/>• Additional color cost<br/>• Imprint side <br/>• Product Dimensions<br/><br/>Attached are photos showing ideas we have come up with to display the information. <br/><br/>The link below shows how our product pages is currently laid out. <br/><br/>Link to webpage: https://www.brightharborgoods-example.com/non-woven-reusable-promo-totes.html<br/>

Number of Pages Required

1 page

Colors
33b8a4
33a6d7
3277b5
fece3e
f9a040
a3cd3a

Requirements
Must have
• • Product price per piece & price breaks
• • Set up cost
• • Additional color cost
• • Imprint side
• • Product Dimensions

```html
<!DOCTYPE html>
<html lang="en">
<head>
<meta charset="utf-8">
<title>Bright Harbor Goods – Non-Woven Reusable Promo Totes</title>
<link href="https://fonts.googleapis.com/css2?family=Roboto:wght@400;500;700&family=Open+Sans:wght@400;600&display=swap" rel="stylesheet">
<style>
:root{
  --teal:#33b8a4;--sky:#33a6d7;--navy:#3277b5;--sun:#fece3e;--orange:#f9a040;--lime:#a3cd3a;
  --ink:#222;--muted:#555;--line:#d6dbe2;--panel:#eef0f4;--footer:#2d5fa8;--footer-dark:#244f90;
}
*{box-sizing:border-box;margin:0;padding:0}
html,body{width:1200px;height:3173px;overflow:hidden}
body{position:relative;font-family:'Roboto',sans-serif;color:var(--ink);background:#fff}
.abs{position:absolute}
.topbar{left:0;top:0;width:1200px;height:44px;background:#f2f2f2}
.topbar .social{left:140px;top:15px;display:flex;gap:24px}
.topbar .social span{width:14px;height:14px;border-radius:50%;background:#8a8a8a;display:block}
.topnav{right:130px;top:0;display:flex;height:44px}
.topnav a{font-size:13px;color:#444;text-decoration:none;padding:0 15px;line-height:44px;border-left:1px solid #ddd}
.topnav a:first-child{border-left:none}
.header{left:0;top:44px;width:1200px;height:108px}
.brand{left:127px;top:40px;font-size:28px;font-weight:700;color:var(--teal);line-height:1;white-space:nowrap}
.search{left:409px;top:34px;width:334px;height:44px;border:1px solid #aaa;border-radius:22px;display:flex;align-items:center;padding-left:20px;gap:10px;font-size:14px;color:#777}
.phone{left:770px;top:40px;display:flex;align-items:center;gap:8px;font-size:23px;font-weight:700;color:var(--navy)}
.cart{left:1020px;top:34px}
.mainnav{left:0;top:152px;width:1200px;height:62px;background:linear-gradient(#3dbfa9,#2faa98);display:flex;padding-left:120px}
.mainnav a{color:#fff;font-weight:700;font-size:16px;text-decoration:none;line-height:62px;padding:0 24px;border-right:1px solid rgba(255,255,255,.25)}
.mainnav a:first-child{background:#2a9e8d}
.crumb{left:0;top:214px;width:1200px;height:32px;background:var(--lime);color:#fff;font-size:13px;line-height:32px;padding-left:130px}
.hero{left:0;top:246px;width:1200px;height:313px;background:linear-gradient(90deg,#dfe5e8 0%,#b9cbd6 45%,#6d9dbd 70%,#a9c1d1 100%)}
.hero h1{position:absolute;left:140px;top:134px;font-size:33px;font-weight:700;color:#1d3d33}
.gallery-main{left:136px;top:632px;width:405px;height:331px;border:1px solid #ccc;display:flex;align-items:center;justify-content:center}
.gallery-main div{width:150px;height:210px;background:linear-gradient(#2c8bd0,#1b6fae);border-radius:4px}
.thumb{width:78px;height:74px;border:1px solid #e4e4e4;display:flex;align-items:center;justify-content:center}
.thumb i{width:44px;height:52px;border-radius:3px;display:block}
.prod-title{left:571px;top:628px;font-size:27px;font-weight:500}
.sku{left:571px;top:674px;font-size:20px}
.spec{left:571px;top:708px;font-size:13px;display:flex;gap:14px;align-items:center;white-space:nowrap}
.stars{color:var(--orange);letter-spacing:1px}
.price{left:571px;width:551px;border:1px solid #9bc8e6;font-size:12px}
.price .head{height:38px;line-height:38px;text-align:center;color:#fff;font-weight:700;font-size:13px}
.price table{width:100%;border-collapse:collapse}
.price td{border:1px solid var(--line);text-align:center;height:29px;color:#444}
.price td.l{font-weight:700;width:74px;color:#222}
.price .note{background:var(--sun);height:23px;line-height:23px;text-align:center;font-weight:700;font-size:11px}
.price .extra{display:flex;justify-content:flex-end;gap:16px;padding:0 3px;height:34px;align-items:center;font-size:11px;color:#555;background:#f6f7f9;white-space:nowrap}
.btn{top:1111px;height:47px;width:181px;color:#fff;font-weight:700;font-size:14px;display:flex;align-items:center;justify-content:center}
.tabs{left:0;top:1238px;width:1200px;height:56px;background:linear-gradient(var(--sky),#3a9fd8);display:flex;padding-left:181px}
.tabs a{color:#fff;font-weight:700;font-size:15px;text-decoration:none;line-height:56px;padding:0 24px}
.tabs a.on{background:#e8eef5;color:var(--navy);width:111px;text-align:center;padding:0}
.details{left:0;top:1294px;width:1200px;height:598px;background:var(--panel)}
.details h2{position:absolute;left:184px;top:52px;font-size:21px;font-weight:500}
.row{position:absolute;left:186px;font-size:14px;display:flex}
.row b{font-weight:400;width:166px}
.feat{position:absolute;font-size:14px}
.feat:before{content:"›";color:var(--navy);font-weight:700;font-size:20px;margin-right:6px;vertical-align:-1px}
.sec-title{left:0;width:1200px;text-align:center;font-size:25px;font-weight:700}
.review{top:1995px;width:304px;height:192px;background:linear-gradient(90deg,var(--orange),#fbbd3c);color:#fff;padding:36px 16px 36px 36px;font-family:'Open Sans',sans-serif}
.review .stars{color:#fff;font-size:16px;letter-spacing:3px}
.review h4{font-size:15px;font-weight:600;margin:8px 0 4px;font-family:'Roboto',sans-serif}
.review p{font-size:12.5px;line-height:22px;color:#fff6e6;white-space:nowrap}
.arrow{font-size:46px;color:#999;line-height:1}
.arrow.on{color:var(--navy)}
.recs{left:0;top:2260px;width:1200px;height:525px;background:#f1f3f6}
.card{top:2372px;width:239px;height:336px;background:#fff;border:1px solid #ddd;box-shadow:0 2px 4px rgba(0,0,0,.08);text-align:center}
.card .ph{width:170px;height:150px;margin:26px auto 24px;border-radius:4px}
.card .sz{color:#8cba2a;font-weight:700;font-size:13.5px}
.card p{font-size:13.5px;margin-top:8px;color:#333}
.card .stars{font-size:18px;margin-top:6px}
.card small{display:block;font-size:11px;margin-top:6px}
.footer{left:0;top:2785px;width:1200px;height:335px;background:var(--footer);color:#fff;font-family:'Open Sans',sans-serif}
.footer .fbrand{position:absolute;left:158px;top:64px;font-family:'Roboto',sans-serif;font-size:30px;font-weight:700}
.footer .about{position:absolute;left:158px;top:146px;width:300px;font-size:12.5px;line-height:22px;color:#e6eef9}
.footer .circles{position:absolute;left:158px;top:248px;display:flex;gap:8px}
.footer .circles span{width:32px;height:32px;border:2px solid #fff;border-radius:50%;display:block}
.fcol{position:absolute;top:68px;font-size:12.5px;line-height:23px;color:#e6eef9}
.fcol h5{font-family:'Roboto',sans-serif;font-size:15px;font-weight:500;color:#fff;margin-bottom:4px;letter-spacing:.3px}
.copy{left:0;top:3120px;width:1200px;height:53px;background:var(--footer-dark);color:#e6eef9;font-size:13px;text-align:center;line-height:53px;font-family:'Open Sans',sans-serif}
</style>
</head>
<body>

<div class="abs topbar">
  <div class="abs social"><span></span><span></span><span></span><span></span><span></span></div>
  <nav class="abs topnav"><a>HOME</a><a>ABOUT US</a><a>CONTACT US</a><a>BLOG</a></nav>
</div>

<header class="abs header">
  <div class="abs brand">Bright Harbor Goods</div>
  <div class="abs search">
    <svg width="16" height="16" viewBox="0 0 16 16"><circle cx="6.5" cy="6.5" r="5" fill="none" stroke="#33b8a4" stroke-width="2"/><line x1="10" y1="10" x2="15" y2="15" stroke="#33b8a4" stroke-width="2"/></svg>
    Search Entire Store
  </div>
  <div class="abs phone">
    <svg width="26" height="26" viewBox="0 0 24 24"><path d="M6 2l3 4-2 2c1 3 4 6 7 7l2-2 4 3-2 4C10 20 4 14 2 6z" fill="#a3cd3a"/></svg>
    1-800-555-0142
  </div>
  <svg class="abs cart" width="44" height="42" viewBox="0 0 44 42">
    <path d="M2 8h6l5 20h20l5-14H11" fill="none" stroke="#3277b5" stroke-width="3"/>
    <circle cx="16" cy="35" r="3" fill="#3277b5"/><circle cx="31" cy="35" r="3" fill="#3277b5"/>
    <circle cx="34" cy="10" r="9" fill="#f9a040"/><text x="34" y="14" font-size="11" fill="#fff" text-anchor="middle" font-family="Roboto">0</text>
  </svg>
</header>

<nav class="abs mainnav"><a>REUSABLE BAGS ▾</a><a>SEED PAPER ▾</a><a>REUSABLE BOTTLES ▾</a><a>LANYARDS ▾</a><a>ECO PROMO ITEMS ▾</a></nav>
<div class="abs crumb">Home &nbsp;›&nbsp; Non-Woven Reusable Promo Totes</div>

<section class="abs hero" role="img" aria-label="Photo of a woman in a sun hat carrying a white reusable tote bag">
  <h1>REUSABLE BAGS</h1>
</section>

<div class="abs gallery-main" role="img" aria-label="Royal blue non-woven tote bag"><div></div></div>
<div class="abs" style="left:132px;top:986px;display:flex;gap:6px">
  <div class="thumb"><i style="background:#222"></i></div><div class="thumb"><i style="background:#1f4a30"></i></div><div class="thumb"><i style="background:#23915a"></i></div><div class="thumb"><i style="background:#7dd04a"></i></div><div class="thumb"><i style="background:#1b74b8"></i></div>
</div>
<div class="abs" style="left:132px;top:1084px;display:flex;gap:6px">
  <div class="thumb"><i style="background:#1f8a8a"></i></div><div class="thumb"><i style="background:#3dcf5a"></i></div><div class="thumb"><i style="background:#1d3b8a"></i></div><div class="thumb"><i style="background:#4fd39c"></i></div><div class="thumb"><i style="background:#3b0fbf"></i></div>
</div>

<h1 class="abs prod-title">Non-Woven Reusable Promo Totes</h1>
<div class="abs sku">SKU: PP2</div>
<div class="abs spec"><span>Size: 13" W x 14" H x 7" D</span><span>Thickness: 100 GSM</span><span><span class="stars">★★★★★</span> 38 Review(s) | Add Review</span></div>

<div class="abs price" style="top:751px">
  <div class="head" style="background:linear-gradient(var(--sky),#2e8fcb)">IN-STOCK</div>
  <table>
    <tr><td class="l">QTY</td><td>1</td><td>100+</td><td>250+</td><td>500+</td><td>1,000+</td><td>2,500+</td><td>5,000+</td></tr>
    <tr><td class="l">PRICE</td><td>$0.69</td><td>$1.46</td><td>$1.35</td><td>$1.30</td><td>$1.26</td><td>$1.23</td><td>$1.19</td></tr>
  </table>
  <div class="note">Includes 1 Imprint Color</div>
  <div class="extra"><span>8"WX8"H</span><span>Add Color</span><span>$0.45 each</span><span>Full Color Imp.300+</span><span>$1.00 each</span><span>$45 per each</span></div>
</div>

<div class="abs price" style="top:928px">
  <div class="head" style="background:linear-gradient(var(--lime),#8fbb2a)">OVERSEAS</div>
  <table>
    <tr><td class="l">QTY</td><td>1</td><td>1000+</td><td>3000+</td><td>5000+</td><td>10,000+</td><td>25,000+</td><td>50,000+</td></tr>
    <tr><td class="l">PRICE</td><td>$0.69</td><td>$1.14</td><td>$0.94</td><td>$0.89</td><td>$0.84</td><td>$0.74</td><td>$0.69</td></tr>
  </table>
  <div class="note">FREE 1 Color, 2 Location Imprint</div>
  <div class="extra" style="justify-content:space-between;padding:0 2px 0 28px"><span>Size</span><span>Unimited</span><span>Add Color$0.45 each</span><span>Full Color Imp.</span><span>Call &nbsp;&nbsp; Fee</span><span>$45 per each</span></div>
</div>

<div class="abs btn" style="left:573px;background:var(--navy)">REQUEST A QUOTE</div>
<div class="abs btn" style="left:762px;background:var(--orange)">BUY NOW</div>
<div class="abs btn" style="left:951px;background:var(--lime)">ORDER FREE SAMPLE</div>

<nav class="abs tabs"><a class="on">DETAILS</a><a>REVIEWS</a><a>ADDTIONAL INFO</a><a>SHIPPING ESTIMATOR</a></nav>

<section class="abs details">
  <h2>Non-Woven Promotional Tote Bags Wholesale</h2>
  <div class="row" style="top:110px"><b>Name</b>Non-Woven Reusable Promo Totes</div>
  <div class="row" style="top:151px"><b>SKU</b>PP2</div>
  <div class="row" style="top:192px"><b>Size</b>13" W x 14" H x 7" D</div>
  <div class="row" style="top:233px"><b>Thickness</b>100 GSM</div>
  <div class="row" style="top:274px"><b>Available Colors</b>Black, Hunter Green, Kelly Green, Lime Green, Maui Blue, Navy Blue, Purple, Red, Royal Blue, Tan, Teal &amp; Yellow</div>
  <div class="row" style="top:315px"><b>Imprint Area</b>8" W x 8" H</div>
  <div class="row" style="top:356px"><b>Key Features</b></div>
  <div class="feat" style="left:352px;top:354px">Spacious Main Compartment, 1274 Cubic Inches</div>
  <div class="feat" style="left:352px;top:389px">22" Carry Straps</div>
  <div class="feat" style="left:352px;top:424px">Made from 100 GSM Non-Woven Polypropylene</div>
  <div class="feat" style="left:352px;top:459px">Eco-Friendly and 100% Recyclable</div>
  <div class="feat" style="left:352px;top:494px">Removable Hard Bottom Insert at the Base</div>
  <div class="feat" style="left:741px;top:354px">5 Day Standard Production / RUSH service available</div>
  <div class="feat" style="left:741px;top:389px">10 Day Production for Full Color Artwork</div>
  <div class="feat" style="left:741px;top:424px">8" Wide x 8" High Imprint Area</div>
  <div class="feat" style="left:741px;top:459px">Made From Recycled Content</div>
</section>

<h2 class="abs sec-title" style="top:1934px">CUSTOMER REVIEWS</h2>
<div class="abs arrow" style="left:62px;top:2068px">‹</div>
<div class="abs review" style="left:124px"><div class="stars">★★★★★</div><h4>Review by Maya R</h4><p>Lorem ipsum dolor sit amet conse<br>ctetuer adipiscing elit Nam cursus Morbi<br>ut mi Nullam enim leo egestas id</p></div>
<div class="abs review" style="left:456px"><div class="stars">★★★★★</div><h4>Review by Maya R</h4><p>Lorem ipsum dolor sit amet conse<br>ctetuer adipiscing elit Nam cursus Morbi<br>ut mi Nullam enim leo egestas id</p></div>
<div class="abs review" style="left:784px"><div class="stars">★★★★★</div><h4>Review by Maya R</h4><p>Lorem ipsum dolor sit amet conse<br>ctetuer adipiscing elit Nam cursus Morbi<br>ut mi Nullam enim leo egestas id</p></div>
<div class="abs arrow on" style="left:1110px;top:2068px">›</div>

<section class="abs recs">
  <h2 class="abs sec-title" style="top:46px">RECOMMENDED PRODUCTS</h2>
</section>
<div class="abs arrow" style="left:48px;top:2520px">‹</div>
<div class="abs card" style="left:98px"><div class="ph" role="img" aria-label="Blue and red branded tote bags" style="background:linear-gradient(90deg,#1f62a8 50%,#d8262e 50%)"></div><div class="sz">Size: 13" W x 15" H x 10" D</div><p>As Low As: $0.75</p><p>SKU: PP3A</p><div class="stars">★★★★★</div><small>(27 Reviews)</small></div>
<div class="abs card" style="left:352px"><div class="ph" role="img" aria-label="Green and tan branded tote bags" style="background:linear-gradient(90deg,#2da84a 50%,#cdb88a 50%)"></div><div class="sz">Size: 13" W x 15" H x 10" D</div><p>As Low As: $0.75</p><p>SKU: PP3A</p><div class="stars">★★★★★</div><small>(27 Reviews)</small></div>
<div class="abs card" style="left:610px"><div class="ph" role="img" aria-label="Green and red branded tote bags" style="background:linear-gradient(90deg,#34c04a 50%,#e02a2a 50%)"></div><div class="sz">Size: 13" W x 15" H x 10" D</div><p>As Low As: $0.75</p><p>SKU: PP3A</p><div class="stars">★★★★★</div><small>(27 Reviews)</small></div>
<div class="abs card" style="left:864px"><div class="ph" role="img" aria-label="Purple and tan branded tote bags" style="background:linear-gradient(90deg,#5b3b9a 50%,#d9c08f 50%)"></div><div class="sz">Size: 13" W x 15" H x 10" D</div><p>As Low As: $0.75</p><p>SKU: PP3A</p><div class="stars">★★★★★</div><small>(27 Reviews)</small></div>
<div class="abs arrow on" style="left:1112px;top:2520px">›</div>

<footer class="abs footer">
  <div class="fbrand">Bright Harbor Goods</div>
  <p class="about">Bright Harbor Goods is an eco-friendly company that specializes in manufacturing custom bags. BHG was founded in 2009 and has strived to make the world a better place ever since.</p>
  <div class="circles"><span></span><span></span><span></span><span></span><span></span><span></span></div>
  <div class="fcol" style="left:507px"><h5>USEFUL LINKS</h5>Customer Service<br>Our Story<br>Site Map<br>FTC Disclosure<br>Privacy Policy<br>Contact Us<br>Art &amp; Imprint Policy<br>Free Rush</div>
  <div class="fcol" style="left:683px"><h5>WHY BUY FROM US</h5>Reusable Bag Stats<br>Best Price Guarantee<br>Return &amp; Refund Policy<br>Shipping Policy<br>In-Stock &amp; Custom Production<br>Frequently Asked Questions</div>
  <div class="fcol" style="left:894px"><h5>ADDRESS</h5>48 Lantern Wharf Rd., Suite 3<br>Port Ellery, FL 33901<br>Phone: 1-800-555-0142<br>Email: hello@brightharborgoods-example.com</div>
</footer>
<div class="abs copy">© 2020 BrightHarborGoods.com</div>

</body>
</html>
```